Real Estate Webpage Design

We have an existing website: ferndaleestatecollective.com.au
We focus customised service mainly on Property Management and second-hand property sales.
We are not entirely happy about the current design and layout can stay roughly the same as the back end coding is linked to a CRM system.
We would like to see the design are more reachable to our clients and appearing.
Please check our Website Design Draft for more details.

Industry/Entity Type

Real estate Agency

Number of Pages Required

5+ page

Font styles to use
Sans Serif

Colors

Designer to choose colors to be used in the design.

```html
<!DOCTYPE html>
<html lang="en">
<head>
<meta charset="utf-8">
<title>Ferndale Estate Collective</title>
<link href="https://fonts.googleapis.com/css2?family=Poppins:wght@400;500;600&display=swap" rel="stylesheet">
<style>
:root{
  --gold:#E6B64A;
  --gold-dark:#D9A534;
  --navy:#1F3352;
  --navy-deep:#182A45;
  --cream:#F8F0DC;
  --soft:#F6F6F8;
  --ink:#1C1C1C;
  --muted:#7A7A7A;
  --line:#E3E3E3;
  --white:#FFFFFF;
}
*{box-sizing:border-box;margin:0;padding:0}
html,body{width:1200px;height:4959px;overflow:hidden}
body{font-family:"Poppins",sans-serif;color:var(--ink);background:var(--white)}
.page{position:relative;width:1200px;height:4959px;overflow:hidden}
.abs{position:absolute}
.btn{position:absolute;display:flex;align-items:center;justify-content:center;background:var(--gold);color:var(--white);font-size:12px;border:1px solid var(--gold-dark);box-shadow:2px 2px 0 var(--gold-dark)}
.photo{position:absolute}
h2.title{font-weight:600;font-size:26px;color:var(--ink)}
p.body{font-size:12.5px;line-height:22px;color:var(--muted)}

.hero{position:absolute;left:0;top:0;width:1200px;height:578px;background:linear-gradient(100deg,#F7F7F7 0%,#EDEDED 45%,#DCDCDC 70%,#C9C9C9 100%)}
.brand{position:absolute;display:flex;align-items:center;gap:12px}
.brand-mark{width:50px;height:50px;background:var(--gold)}
.brand-name{font-weight:600;font-size:38px;color:var(--gold);line-height:1}
.brand-sub{font-size:10px;letter-spacing:1px;color:var(--navy);margin-top:2px}
.nav{position:absolute;left:435px;top:28px;font-size:13px;color:var(--ink)}
.nav span{position:absolute;white-space:nowrap}
.hero-title{position:absolute;left:62px;top:190px;width:620px;font-size:40px;font-weight:600;line-height:48px}
.hero-title em{font-style:normal;color:var(--gold)}
.hero-lead{position:absolute;left:62px;top:298px;width:540px;font-size:13px;line-height:23px;color:var(--muted)}

.search{position:absolute;left:60px;top:578px;width:1080px;height:87px;background:var(--white);box-shadow:0 4px 14px rgba(0,0,0,.08);border-top:1px solid var(--line)}
.field{position:absolute;top:16px;height:54px}
.field b{display:block;font-weight:500;font-size:13px;color:var(--ink)}
.field i{display:block;font-style:normal;font-size:11px;color:var(--muted);margin-top:12px}
.field svg{position:absolute;right:0;top:34px}
.field.sep{border-right:1px solid var(--line)}
.search-go{position:absolute;left:1009px;top:17px;width:54px;height:56px;background:var(--gold);display:flex;align-items:center;justify-content:center}

.feature{position:absolute;width:186px;height:164px;background:var(--white);box-shadow:0 2px 12px rgba(0,0,0,.09);text-align:center;font-size:15px;font-weight:500}
.feature svg{display:block;margin:34px auto 12px}
.eyebrow{font-size:12px;color:var(--gold)}

.services{position:absolute;left:60px;top:1223px;width:1080px;height:930px;background:var(--soft)}
.badge-square{position:absolute;left:567px;top:1658px;width:62px;height:62px;background:var(--white);border:3px solid var(--gold)}

.agents{position:absolute;left:0;top:2234px;width:1200px;height:437px;background:var(--cream)}

.tab{position:absolute;top:2826px;height:35px;display:flex;align-items:center;justify-content:center;font-size:12px;border:1px solid #BFBFBF;background:var(--white)}
.tab.on{background:var(--gold);color:var(--white);border-color:var(--gold)}
.card{position:absolute;top:2900px;width:341px;height:390px;background:var(--white);box-shadow:0 2px 12px rgba(0,0,0,.1)}
.card .img{position:absolute;left:0;top:0;width:341px;height:232px}
.card .bar{position:absolute;left:0;top:0;width:341px;height:42px;background:rgba(24,42,69,.85);color:var(--white)}
.card .bar b{position:absolute;left:66px;top:4px;font-size:13px;font-weight:600}
.card .bar span{position:absolute;left:66px;top:22px;font-size:11px;white-space:nowrap}
.card .price{position:absolute;left:12px;top:200px;color:var(--white);font-weight:600;font-size:15px}
.card .next{position:absolute;right:18px;top:190px;width:26px;height:26px;border:1px solid var(--white);background:rgba(0,0,0,.25)}
.specs{position:absolute;left:20px;top:248px;display:flex;gap:18px;font-size:12px;align-items:center}
.specs span{display:flex;align-items:center;gap:6px}
.card h4{position:absolute;left:20px;top:282px;font-size:15px;font-weight:600}
.card .date{position:absolute;left:20px;top:310px;font-size:12px;color:var(--gold)}
.card .foot{position:absolute;left:0;top:346px;width:341px;height:44px;border-top:1px solid var(--line)}
.card .avatar{position:absolute;left:18px;top:12px;width:28px;height:28px;background:#8A8F98}
.card .agent{position:absolute;left:58px;top:16px;font-size:12px}
.card .tools{position:absolute;right:18px;top:16px;display:flex;gap:10px}

.voices{position:absolute;left:0;top:3453px;width:1200px;height:374px;background:linear-gradient(180deg,#203655,#1B2F4C)}
.voices h2{position:absolute;left:0;width:1200px;top:50px;text-align:center;color:var(--white);font-size:26px;font-weight:600}
.voices p{position:absolute;left:370px;top:134px;width:460px;text-align:center;color:var(--white);font-size:12.5px;line-height:22.5px}
.voices .who{position:absolute;left:0;width:1200px;top:310px;text-align:center;color:var(--gold);font-size:13px}
.arrow{position:absolute;top:185px;width:32px;height:32px;display:flex;align-items:center;justify-content:center}

.news{position:absolute;width:520px;height:146px}
.news .img{position:absolute;left:0;top:0;width:227px;height:146px}
.news .meta{position:absolute;left:256px;top:14px;font-size:11px;color:var(--muted);display:flex;gap:18px}
.news h3{position:absolute;left:256px;top:42px;width:270px;font-size:16px;font-weight:500;line-height:28px}
.news a{position:absolute;left:256px;top:120px;font-size:12px;color:var(--gold);text-decoration:none}

.cta{position:absolute;left:0;top:4333px;width:1200px;height:282px;background:var(--gold)}
.cta h2{position:absolute;left:0;width:1200px;top:108px;text-align:center;color:var(--white);font-size:22px;font-weight:600;line-height:34px}
.cta .go{position:absolute;left:497px;top:195px;width:206px;height:34px;background:var(--navy);color:var(--white);font-size:12px;display:flex;align-items:center;justify-content:center;border:1px solid var(--white)}
.footer{position:absolute;left:0;top:4615px;width:1200px;height:344px;background:var(--navy);color:var(--white)}
.footer h5{position:absolute;top:42px;font-size:12px;font-weight:500;color:var(--gold)}
.footer .links{position:absolute;left:329px;top:78px;font-size:11px;line-height:27px}
.footer .links div::before{content:"⟶";margin-right:8px;color:var(--white)}
.footer .contact{position:absolute;left:612px;font-size:11px;display:flex;gap:12px}
.social{position:absolute;top:102px;width:38px;height:38px;border-radius:50%;border:1.5px solid var(--white)}
.social.first{background:var(--gold);border-color:var(--gold)}
.legal{position:absolute;left:62px;top:320px;width:1076px;font-size:11px;display:flex}
.legal .right{margin-left:auto;display:flex;gap:26px}
.rule{position:absolute;left:62px;top:304px;width:1076px;height:1px;background:rgba(255,255,255,.2)}
</style>
</head>
<body>
<div class="page">

  <div class="hero" role="img" aria-label="Bright living room with a white sofa, side table, vase of flowers and wall shelves"></div>
  <div class="brand" style="left:62px;top:16px">
    <div class="brand-mark"></div>
    <div>
      <div class="brand-name">Ferndale</div>
      <div class="brand-sub">EstateCollective</div>
    </div>
  </div>
  <nav class="nav">
    <span style="left:0">Home</span>
    <span style="left:70px">About Us</span>
    <span style="left:152px">Leasing</span>
    <span style="left:230px">Buy</span>
    <span style="left:282px">Sell</span>
    <span style="left:332px">Our Team</span>
    <span style="left:422px">Blog</span>
    <span style="left:478px">Contact Us</span>
  </nav>
  <div class="btn" style="left:1013px;top:19px;width:125px;height:35px;font-size:13px">Add Properties</div>
  <section>
    <h1 class="hero-title">Welcome To <em>Ferndale</em> Property Group</h1>
    <p class="hero-lead">Lorem Ipsum is simply dummy text of the printing and typesetting industry. Lorem Ipsum has been the industry's standard dummy text ever since the 1500s, when an unknown printer</p>
    <div class="btn" style="left:62px;top:397px;width:145px;height:31px;font-size:13px">See All Properties</div>
  </section>

  <div class="search">
    <div class="field sep" style="left:25px;width:205px"><b>Categories</b><i>Property Category</i>
      <svg width="12" height="8" viewBox="0 0 12 8"><path d="M1 1l5 5 5-5" fill="none" stroke="#333" stroke-width="1.5"/></svg></div>
    <div class="field sep" style="left:250px;width:170px"><b>City</b><i>Property City</i>
      <svg width="12" height="8" viewBox="0 0 12 8"><path d="M1 1l5 5 5-5" fill="none" stroke="#333" stroke-width="1.5"/></svg></div>
    <div class="field sep" style="left:437px;width:180px"><b>Area</b><i>Property Area</i>
      <svg width="12" height="8" viewBox="0 0 12 8"><path d="M1 1l5 5 5-5" fill="none" stroke="#333" stroke-width="1.5"/></svg></div>
    <div class="field sep" style="left:633px;width:180px"><b>Type</b><i>Apartment</i>
      <svg width="12" height="8" viewBox="0 0 12 8"><path d="M1 1l5 5 5-5" fill="none" stroke="#333" stroke-width="1.5"/></svg></div>
    <div class="field" style="left:822px;width:160px"><b>Price Range</b><i>1-50,00,000</i>
      <svg width="12" height="8" viewBox="0 0 12 8"><path d="M1 1l5 5 5-5" fill="none" stroke="#333" stroke-width="1.5"/></svg></div>
    <div class="search-go"><svg width="24" height="24" viewBox="0 0 24 24"><circle cx="10" cy="10" r="7" fill="none" stroke="#fff" stroke-width="2"/><path d="M15 15l6 6" stroke="#fff" stroke-width="2"/></svg></div>
  </div>

  <div class="feature" style="left:60px;top:751px">
    <svg width="52" height="52" viewBox="0 0 52 52"><rect x="10" y="6" width="26" height="36" fill="none" stroke="#222" stroke-width="2"/><path d="M15 16h16M15 23h16M15 30h12" stroke="#222" stroke-width="2"/><circle cx="38" cy="12" r="7" fill="none" stroke="var(--gold)" stroke-width="2"/></svg>
    Great Experience</div>
  <div class="feature" style="left:262px;top:751px">
    <svg width="52" height="52" viewBox="0 0 52 52"><rect x="16" y="6" width="20" height="14" fill="none" stroke="var(--gold)" stroke-width="2"/><path d="M4 26l10-4 12 8 12-8 10 4M14 22l-6 16M38 22l6 16M18 34l8 6 8-6" fill="none" stroke="#222" stroke-width="2"/></svg>
    Safety Deals</div>
  <div class="feature" style="left:60px;top:928px">
    <svg width="52" height="52" viewBox="0 0 52 52"><circle cx="24" cy="24" r="9" fill="none" stroke="#222" stroke-width="2"/><path d="M10 24a14 14 0 0 1 28 0M8 44c4-8 28-8 32 0" fill="none" stroke="#222" stroke-width="2"/><rect x="34" y="4" width="14" height="10" fill="none" stroke="var(--gold)" stroke-width="2"/></svg>
    Comprehensive<br>Support</div>
  <div class="feature" style="left:262px;top:928px">
    <svg width="52" height="52" viewBox="0 0 52 52"><circle cx="26" cy="16" r="9" fill="none" stroke="var(--gold)" stroke-width="2"/><path d="M4 36h12l10 6 18-10-4-4-12 6M4 44h10" fill="none" stroke="#222" stroke-width="2"/></svg>
    Property<br>Management</div>

  <section>
    <div class="abs eyebrow" style="left:510px;top:760px">About Us</div>
    <h2 class="abs title" style="left:510px;top:780px">Who Is Ferndale?</h2>
    <p class="abs body" style="left:510px;top:823px;width:490px">Ferndale is named for "the home, the house", buying a property is one of the most expensive expenses and important assets for people. Ferndale is a real estate company located in Brookvale Park, Westmere.</p>
    <p class="abs body" style="left:510px;top:898px;width:490px">Being a portfolio sales agent and property manager, coupled with our high-profile international real estate experience, Ferndale is considered a market leader on the cutting edge with deep industry knowledge, ranging from landlord-tenant relationships, residential purchases.</p>
    <div class="abs" style="left:510px;top:998px;font-size:13px">Have question? Call us <span style="color:var(--gold);font-size:16px;font-weight:500">&nbsp;02 6100 4820</span></div>
    <div class="btn" style="left:510px;top:1050px;width:130px;height:33px">More About Us</div>
  </section>

  <div class="services"></div>
  <div class="photo" role="img" aria-label="Agent shaking hands with clients across a desk" style="left:599px;top:1223px;width:541px;height:466px;background:linear-gradient(135deg,#F2EFEB,#D7CEC4 60%,#8A7664)"></div>
  <div class="photo" role="img" aria-label="Open-plan living room with timber wall and large windows" style="left:60px;top:1689px;width:539px;height:464px;background:linear-gradient(135deg,#8C6A4E,#B9AFA4 45%,#D8D4CE 75%,#6E6F6A)"></div>
  <div class="badge-square"></div>
  <section>
    <h2 class="abs title" style="left:125px;top:1290px">Property Management</h2>
    <p class="abs body" style="left:125px;top:1356px;width:410px">Lorem Ipsum is simply dummy text of the printing and typesetting industry. Lorem Ipsum has been the industry's standard dummy text ever since the 1500s, when an unknown printer took a galley of type and scrambled it to make a type specimen book.</p>
    <p class="abs body" style="left:125px;top:1491px;width:410px">It has survived not only five centuries, but also the leap into electronic typesetting, remaining essentially unchanged.</p>
    <div class="btn" style="left:125px;top:1566px;width:106px;height:33px">Contact Us</div>
  </section>
  <section>
    <h2 class="abs title" style="left:664px;top:1756px">Second-hand property sales</h2>
    <p class="abs body" style="left:664px;top:1823px;width:410px">Lorem Ipsum is simply dummy text of the printing and typesetting industry. Lorem Ipsum has been the industry's standard dummy text ever since the 1500s, when an unknown printer took a galley of type and scrambled it to make a type specimen book.</p>
    <p class="abs body" style="left:664px;top:1959px;width:410px">It has survived not only five centuries, but also the leap into electronic typesetting, remaining essentially unchanged.</p>
    <div class="btn" style="left:664px;top:2038px;width:89px;height:33px">Sell Now</div>
  </section>

  <div class="agents"></div>
  <section>
    <h2 class="abs title" style="left:62px;top:2298px">Our Agents</h2>
    <p class="abs body" style="left:62px;top:2368px;width:485px;color:#555">Lorem Ipsum is simply dummy text of the printing and typesetting industry. Lorem Ipsum has been the industry's standard dummy text ever since the 1500s, when an unknown printer took a galley of type and scrambled it to make a type specimen book. It has survived not only five centuries, but also the leap into electronic typesetting, remaining essentially unchanged. It was popularised in the 1960s with the release of Letraset sheets.</p>
    <div class="btn" style="left:62px;top:2568px;width:104px;height:32px">Our Agents</div>
    <div class="photo" role="img" aria-label="Agent portrait" style="left:713px;top:2321px;width:133px;height:129px;background:linear-gradient(180deg,#EDEDED,#9A9A9A)"></div>
    <div class="photo" role="img" aria-label="Agent portrait" style="left:713px;top:2465px;width:133px;height:124px;background:linear-gradient(180deg,#EDEDED,#9A9A9A)"></div>
    <div class="photo" role="img" aria-label="Agent portrait" style="left:861px;top:2352px;width:133px;height:127px;background:linear-gradient(180deg,#EDEDED,#9A9A9A)"></div>
    <div class="photo" role="img" aria-label="Agent portrait" style="left:861px;top:2492px;width:133px;height:128px;background:linear-gradient(180deg,#EDEDED,#9A9A9A)"></div>
    <div class="photo" role="img" aria-label="Agent portrait" style="left:1007px;top:2290px;width:133px;height:127px;background:linear-gradient(180deg,#EDEDED,#9A9A9A)"></div>
    <div class="photo" role="img" aria-label="Agent portrait" style="left:1007px;top:2429px;width:133px;height:127px;background:linear-gradient(180deg,#EDEDED,#9A9A9A)"></div>
  </section>

  <h2 class="abs title" style="left:0;width:1200px;top:2748px;text-align:center">Listings Available For Latest Property</h2>
  <div class="tab on" style="left:293px;width:106px">For Sale</div>
  <div class="tab" style="left:420px;width:106px">For Lease</div>
  <div class="tab" style="left:547px;width:106px">Open Times</div>
  <div class="tab" style="left:672px;width:108px">Sold</div>
  <div class="tab" style="left:801px;width:106px">Leased</div>

  <div class="card" style="left:60px">
    <div class="img" role="img" aria-label="Apartment building exterior with trees" style="background:linear-gradient(180deg,#6FA3D8,#C9C7C2 55%,#4D5A45)"></div>
    <div class="bar"><svg class="abs" style="left:16px;top:8px" width="26" height="26" viewBox="0 0 26 26"><circle cx="13" cy="13" r="12" fill="none" stroke="#fff"/><path d="M13 6a4 4 0 0 1 4 4c0 3-4 8-4 8s-4-5-4-8a4 4 0 0 1 4-4z" fill="none" stroke="#fff"/></svg><b>Brookvale Park</b><span>Suite 3/12 Wattle Crest Avenue...</span><svg class="abs" style="right:16px;top:10px" width="22" height="22" viewBox="0 0 24 24"><path d="M12 2l3 7 7 .6-5.4 4.7 1.7 7.2L12 17.8 5.7 21.5l1.7-7.2L2 9.6 9 9z" fill="var(--gold)"/></svg></div>
    <div class="price">$369,900+</div><div class="next"></div>
    <div class="specs"><span><svg width="22" height="14"><rect x="1" y="5" width="20" height="8" fill="none" stroke="var(--gold)"/></svg>2</span><span><svg width="18" height="14"><path d="M1 9h16v4H1zM4 9V3h4" fill="none" stroke="var(--gold)"/></svg>2</span><span><svg width="24" height="14"><path d="M2 11h20V7l-4-4H6L2 7z" fill="none" stroke="var(--gold)"/></svg>1</span></div>
    <h4>Next Inspection:</h4><div class="date">Sat 21st May 9:40 Am–10:00 Am</div>
    <div class="foot"><div class="avatar"></div><div class="agent">Mei Lin</div><div class="tools"><svg width="16" height="16"><circle cx="8" cy="8" r="6.5" fill="none" stroke="#333"/><path d="M8 4v4h3" stroke="#333" fill="none"/></svg><svg width="16" height="16"><path d="M2 2l12 12M14 2L2 14" stroke="#333"/></svg><svg width="18" height="14"><rect x="1" y="1" width="16" height="12" fill="none" stroke="#333"/><path d="M1 1l8 6 8-6" fill="none" stroke="#333"/></svg></div></div>
  </div>
  <div class="card" style="left:430px">
    <div class="img" role="img" aria-label="Rooftop pool overlooking the city" style="background:linear-gradient(180deg,#8FA9C2,#6F8EA8 45%,#2D5B8A 70%,#7C6A58)"></div>
    <div class="bar"><svg class="abs" style="left:16px;top:8px" width="26" height="26" viewBox="0 0 26 26"><circle cx="13" cy="13" r="12" fill="none" stroke="#fff"/><path d="M13 6a4 4 0 0 1 4 4c0 3-4 8-4 8s-4-5-4-8a4 4 0 0 1 4-4z" fill="none" stroke="#fff"/></svg><b>Brookvale Park</b><span>Suite 3/12 Wattle Crest Avenue...</span><svg class="abs" style="right:16px;top:10px" width="22" height="22" viewBox="0 0 24 24"><path d="M12 2l3 7 7 .6-5.4 4.7 1.7 7.2L12 17.8 5.7 21.5l1.7-7.2L2 9.6 9 9z" fill="var(--gold)"/></svg></div>
    <div class="price">$5,00,000+</div><div class="next"></div>
    <div class="specs"><span><svg width="22" height="14"><rect x="1" y="5" width="20" height="8" fill="none" stroke="var(--gold)"/></svg>2</span><span><svg width="18" height="14"><path d="M1 9h16v4H1zM4 9V3h4" fill="none" stroke="var(--gold)"/></svg>2</span><span><svg width="24" height="14"><path d="M2 11h20V7l-4-4H6L2 7z" fill="none" stroke="var(--gold)"/></svg>1</span></div>
    <h4>Next Inspection:</h4><div class="date">Sat 21st May 9:40 Am–10:00 Am</div>
    <div class="foot"><div class="avatar"></div><div class="agent">Mei Lin</div><div class="tools"><svg width="16" height="16"><circle cx="8" cy="8" r="6.5" fill="none" stroke="#333"/><path d="M8 4v4h3" stroke="#333" fill="none"/></svg><svg width="16" height="16"><path d="M2 2l12 12M14 2L2 14" stroke="#333"/></svg><svg width="18" height="14"><rect x="1" y="1" width="16" height="12" fill="none" stroke="#333"/><path d="M1 1l8 6 8-6" fill="none" stroke="#333"/></svg></div></div>
  </div>
  <div class="card" style="left:799px">
    <div class="img" role="img" aria-label="Two-storey house with double garage" style="background:linear-gradient(180deg,#9DB7D0,#B9A79A 50%,#5E5A56 80%,#8E7B66)"></div>
    <div class="bar"><svg class="abs" style="left:16px;top:8px" width="26" height="26" viewBox="0 0 26 26"><circle cx="13" cy="13" r="12" fill="none" stroke="#fff"/><path d="M13 6a4 4 0 0 1 4 4c0 3-4 8-4 8s-4-5-4-8a4 4 0 0 1 4-4z" fill="none" stroke="#fff"/></svg><b>Brookvale Park</b><span>Suite 3/12 Wattle Crest Avenue...</span><svg class="abs" style="right:16px;top:10px" width="22" height="22" viewBox="0 0 24 24"><path d="M12 2l3 7 7 .6-5.4 4.7 1.7 7.2L12 17.8 5.7 21.5l1.7-7.2L2 9.6 9 9z" fill="var(--gold)"/></svg></div>
    <div class="price">$5,00,000+</div><div class="next"></div>
    <div class="specs"><span><svg width="22" height="14"><rect x="1" y="5" width="20" height="8" fill="none" stroke="var(--gold)"/></svg>2</span><span><svg width="18" height="14"><path d="M1 9h16v4H1zM4 9V3h4" fill="none" stroke="var(--gold)"/></svg>2</span><span><svg width="24" height="14"><path d="M2 11h20V7l-4-4H6L2 7z" fill="none" stroke="var(--gold)"/></svg>1</span></div>
    <h4>Next Inspection:</h4><div class="date">Sat 21st May 9:40 Am–10:00 Am</div>
    <div class="foot"><div class="avatar"></div><div class="agent">Mei Lin</div><div class="tools"><svg width="16" height="16"><circle cx="8" cy="8" r="6.5" fill="none" stroke="#333"/><path d="M8 4v4h3" stroke="#333" fill="none"/></svg><svg width="16" height="16"><path d="M2 2l12 12M14 2L2 14" stroke="#333"/></svg><svg width="18" height="14"><rect x="1" y="1" width="16" height="12" fill="none" stroke="#333"/><path d="M1 1l8 6 8-6" fill="none" stroke="#333"/></svg></div></div>
  </div>
  <div class="btn" style="left:547px;top:3336px;width:100px;height:33px">View More</div>

  <section class="voices" role="img" aria-label="Night city skyline in navy tones">
    <h2>What Our People Says</h2>
    <svg class="abs" style="left:338px;top:110px" width="40" height="28" viewBox="0 0 40 28"><path d="M2 26V14C2 6 7 2 14 2v6c-4 0-6 2-6 6h6v12zM22 26V14c0-8 5-12 12-12v6c-4 0-6 2-6 6h6v12z" fill="#4A6FA5"/></svg>
    <p>"They are a greatly professional, organized and experienced team with extensive knowledge and understanding of the local market. My husband and I were provided with excellent feedback in a simple language we could understand and advice throughout the house journey and we were very pleased with the results. We highly recommend Ferndale property group to anyone buying, selling or in need of property management in the local area."</p>
    <div class="who">Clara Whitmore</div>
    <div class="arrow" style="left:148px;background:var(--gold)"><svg width="18" height="12" viewBox="0 0 18 12"><path d="M17 6H2M7 1L2 6l5 5" fill="none" stroke="#222" stroke-width="1.6"/></svg></div>
    <div class="arrow" style="left:1007px;background:var(--white)"><svg width="18" height="12" viewBox="0 0 18 12"><path d="M1 6h15M11 1l5 5-5 5" fill="none" stroke="#222" stroke-width="1.6"/></svg></div>
  </section>

  <h2 class="abs title" style="left:0;width:1200px;top:3903px;text-align:center">Our Latest News</h2>
  <article class="news" style="left:60px;top:3983px">
    <div class="img" role="img" aria-label="Apartment living room with balcony view" style="background:linear-gradient(135deg,#6C7F96,#B9B2AA 60%,#5A4B40)"></div>
    <div class="meta"><span>▢ 8 March 2022</span><span>▢ 5 Comments</span></div>
    <h3>Lorem Ipsum is simply dummy text</h3><a>Read More ⟶</a>
  </article>
  <article class="news" style="left:599px;top:3983px">
    <div class="img" role="img" aria-label="Modern kitchen with timber cabinets" style="background:linear-gradient(135deg,#E8E2D8,#C9B49A 60%,#4A4540)"></div>
    <div class="meta" style="left:262px"><span>▢ 8 March 2022</span><span>▢ 5 Comments</span></div>
    <h3 style="left:262px">Lorem Ipsum is simply dummy text</h3><a style="left:262px">Read More ⟶</a>
  </article>
  <article class="news" style="left:60px;top:4160px">
    <div class="img" role="img" aria-label="Empty bright room with timber floor" style="background:linear-gradient(135deg,#F2F0EC,#D6D1C9 60%,#A89C8C)"></div>
    <div class="meta"><span>▢ 8 March 2022</span><span>▢ 5 Comments</span></div>
    <h3>Lorem Ipsum is simply dummy text</h3><a>Read More ⟶</a>
  </article>
  <article class="news" style="left:599px;top:4160px">
    <div class="img" role="img" aria-label="Brick house with front lawn" style="background:linear-gradient(180deg,#6E9BD1,#A99A8C 55%,#6F8A4E)"></div>
    <div class="meta" style="left:262px"><span>▢ 8 March 2022</span><span>▢ 5 Comments</span></div>
    <h3 style="left:262px">Lorem Ipsum is simply dummy text</h3><a style="left:262px">Read More ⟶</a>
  </article>

  <section class="cta">
    <h2>Contact Us If You Want To Sell Your House Or You<br>Have Other Questions</h2>
    <div class="go">Request Free Consultation</div>
  </section>

  <footer class="footer">
    <div class="brand" style="left:62px;top:44px">
      <div class="brand-mark" style="background:var(--white)"></div>
      <div>
        <div class="brand-name" style="color:var(--white)">Ferndale</div>
        <div class="brand-sub" style="color:var(--white)">EstateCollective</div>
      </div>
    </div>
    <p class="abs" style="left:62px;top:124px;width:200px;font-size:11px;line-height:23px">Lorem ipsum dolor sit amet, consectetur adipiscing elit, sed do eiusmod tempor...</p>
    <h5 style="left:329px">Site Map</h5>
    <div class="links"><div>Home</div><div>About Us</div><div>Leasing</div><div>Buy</div><div>Sell</div><div>Our Team</div><div>Blog</div><div>Contact Us</div></div>
    <h5 style="left:612px">Contact Us</h5>
    <div class="contact" style="top:76px"><svg width="22" height="24" viewBox="0 0 22 24"><path d="M11 2a7 7 0 0 1 7 7c0 6-7 13-7 13S4 15 4 9a7 7 0 0 1 7-7z" fill="none" stroke="#fff" stroke-width="1.4"/><circle cx="11" cy="9" r="2.5" fill="none" stroke="#fff" stroke-width="1.4"/></svg><span style="line-height:20px">Suite 9, 22 Wattle Crest Ave, Brookvale<br>Park, WS, 3471</span></div>
    <div class="contact" style="top:126px"><svg width="22" height="22" viewBox="0 0 22 22"><path d="M4 3l4 0 2 5-3 2a11 11 0 0 0 5 5l2-3 5 2v4a2 2 0 0 1-2 2C9 20 2 13 2 5a2 2 0 0 1 2-2z" fill="none" stroke="#fff" stroke-width="1.4"/></svg><span style="line-height:22px;font-weight:600">02 6100 4820<br>02 6100 4821</span></div>
    <div class="contact" style="top:178px"><svg width="22" height="16" viewBox="0 0 22 16"><rect x="1" y="1" width="20" height="14" fill="none" stroke="#fff" stroke-width="1.4"/><path d="M1 1l10 8 10-8" fill="none" stroke="#fff" stroke-width="1.4"/></svg><span>info@ferndale.com</span></div>
    <h5 style="left:890px">Follow On Us</h5>
    <div class="social first" style="left:888px"></div>
    <div class="social" style="left:942px"></div>
    <div class="social" style="left:996px"></div>
    <div class="social" style="left:1050px"></div>
    <div class="rule"></div>
    <div class="legal"><span>2022© Ferndale Properties. All right reserved.</span><div class="right"><span>Privacy</span><span>Complaint Handling &amp; Dispute Resolution</span><span>Due Diligence Checklist</span></div></div>
  </footer>

</div>
</body>
</html>
```